Business Card Design for Occupational Medicine Start Up Company

We need to design a professional business card. We are a healthcare company providing occupational medicine services to blue collar industries. We are professional, efficient and high quality service providers.

Target Market(s)

Blue Collar Industry: Shipbuilding, Ports, Trucking Companies; The Executives and Safety Officers for these companies

Industry/Entity Type

Healthcare

Contact Information for Business Card

Logo, Name, Title, Email, Phone

Other font styles liked:
• Please match our Brand Guide

Requirements
Must have
• Our Company Colors and Logo

```html
<!DOCTYPE html>
<html lang="en">
<head>
<meta charset="utf-8">
<title>Shiftwell Business Card</title>
<link href="https://fonts.googleapis.com/css2?family=Montserrat:wght@600;800;900&family=Poppins:wght@400;500;600&display=swap" rel="stylesheet">
<style>
  :root {
    --navy: #2b3186;
    --sky: #22a3dc;
    --amber: #f2ae45;
    --ink: #262633;
    --rule: #8a8a92;
    --paper: #ffffff;
    --backdrop: #cccccc;
  }
  * { margin: 0; padding: 0; box-sizing: border-box; }
  html, body { width: 800px; height: 1200px; overflow: hidden; }
  body { background: var(--backdrop); position: relative; font-family: "Poppins", sans-serif; }

  .card {
    position: absolute;
    left: 120px;
    width: 560px;
    height: 320px;
    background: var(--paper);
    overflow: hidden;
    box-shadow: 0 4px 14px rgba(0,0,0,0.22);
  }
  .card--front { top: 220px; }
  .card--back { top: 660px; }
  .card__waves { position: absolute; inset: 0; width: 560px; height: 320px; }

  /* front */
  .front__mark {
    position: absolute; left: 255px; top: 96px;
    width: 50px; height: 50px; border-radius: 50%;
    background: var(--navy);
  }
  .front__brand {
    position: absolute; left: 0; right: 0; top: 174px;
    text-align: center;
    font-family: "Montserrat", sans-serif; font-weight: 800;
    font-size: 33px; letter-spacing: 1px; color: var(--navy);
  }
  .front__url {
    position: absolute; left: 0; right: 0; top: 255px;
    text-align: center;
    font-weight: 600; font-size: 15px; letter-spacing: 2.2px; color: var(--ink);
  }
  .front__url .accent { color: var(--navy); }

  /* back */
  .back__brand {
    position: absolute; left: 360px; top: 58px;
    font-family: "Montserrat", sans-serif; font-weight: 800;
    font-size: 18px; letter-spacing: 0.5px; color: var(--navy);
  }
  .holder__name {
    position: absolute; left: 44px; top: 100px;
    font-family: "Montserrat", sans-serif; font-weight: 900;
    font-size: 28px; letter-spacing: 0.5px; color: var(--navy); line-height: 1;
  }
  .holder__name .surname { color: var(--amber); }
  .holder__title {
    position: absolute; left: 44px; top: 134px;
    font-weight: 500; font-size: 11px; color: var(--ink);
  }
  .holder__rule { position: absolute; left: 0; top: 0; width: 560px; height: 320px; }

  .contact { position: absolute; display: flex; align-items: center; gap: 10px;
    font-weight: 500; font-size: 14px; color: var(--ink); }
  .contact svg { width: 28px; height: 30px; flex: none; }
  .contact--phone { left: 42px; top: 181px; }
  .contact--address { left: 42px; top: 217px; }
  .contact--email { left: 284px; top: 181px; }
  .contact--web { left: 284px; top: 217px; }
</style>
</head>
<body>

<section class="card card--front">
  <svg class="card__waves" viewBox="0 0 560 320" aria-hidden="true">
    <path d="M0,0 H100 C40,28 6,90 0,170 Z" fill="var(--sky)"/>
    <path d="M108,0 C46,30 10,92 0,180" fill="none" stroke="var(--navy)" stroke-width="3"/>
    <path d="M118,0 C52,32 14,98 0,198" fill="none" stroke="var(--amber)" stroke-width="4"/>
    <path d="M560,170 C548,248 498,300 420,320 H560 Z" fill="var(--sky)"/>
    <path d="M560,160 C546,244 492,298 408,320" fill="none" stroke="var(--navy)" stroke-width="3"/>
    <path d="M560,145 C543,238 484,296 392,320" fill="none" stroke="var(--amber)" stroke-width="4"/>
  </svg>
  <div class="front__mark"></div>
  <div class="front__brand">SHIFTWELL</div>
  <div class="front__url">www.<span class="accent">shiftwellhealth</span>.com</div>
</section>

<section class="card card--back">
  <svg class="card__waves" viewBox="0 0 560 320" aria-hidden="true">
    <path d="M0,215 C16,268 66,306 122,320 H0 Z" fill="var(--sky)"/>
    <path d="M0,203 C18,262 74,306 136,320" fill="none" stroke="var(--navy)" stroke-width="3"/>
    <path d="M0,188 C20,256 84,306 154,320" fill="none" stroke="var(--amber)" stroke-width="4"/>
    <path d="M560,215 C544,268 494,306 438,320 H560 Z" fill="var(--sky)"/>
    <path d="M560,203 C542,262 486,306 424,320" fill="none" stroke="var(--navy)" stroke-width="3"/>
    <path d="M560,188 C540,256 476,306 406,320" fill="none" stroke="var(--amber)" stroke-width="4"/>
  </svg>

  <div class="back__brand">SHIFTWELL</div>

  <div class="holder__name">MARLO <span class="surname">TRENT</span></div>
  <div class="holder__title">Executives and Safety Officers</div>
  <svg class="holder__rule" viewBox="0 0 560 320" aria-hidden="true">
    <polyline points="230,145 243,145 256,129 515,129" fill="none" stroke="var(--rule)" stroke-width="0.8"/>
  </svg>

  <div class="contact contact--phone">
    <svg viewBox="0 0 28 30" aria-hidden="true">
      <path d="M14,2 L26,7 V15 C26,22 20,27 14,29 C8,27 2,22 2,15 V7 Z" fill="var(--amber)"/>
      <path d="M15,1 L26,6 V14 C26,21 21,26 15,28 C9,26 4,21 4,14 V6 Z" fill="var(--navy)"/>
      <path d="M11,9 L13,9 L14,12 L12.5,13 C13.2,14.8 14.4,16 16,16.6 L17,15 L20,16 V18 C20,19 19,19.5 18,19.3 C14,18.6 11.4,16 10.7,12 C10.5,11 11,10 11,9 Z" fill="#fff"/>
    </svg>
    <span>555.014.2290</span>
  </div>
  <div class="contact contact--address">
    <svg viewBox="0 0 28 30" aria-hidden="true">
      <path d="M14,2 L26,7 V15 C26,22 20,27 14,29 C8,27 2,22 2,15 V7 Z" fill="var(--amber)"/>
      <path d="M15,1 L26,6 V14 C26,21 21,26 15,28 C9,26 4,21 4,14 V6 Z" fill="var(--navy)"/>
      <path d="M15,7 C12.2,7 10.5,9 10.5,11.4 C10.5,14.6 15,20 15,20 C15,20 19.5,14.6 19.5,11.4 C19.5,9 17.8,7 15,7 Z" fill="#fff"/>
      <circle cx="15" cy="11.4" r="1.7" fill="var(--navy)"/>
    </svg>
    <span>Company address 123</span>
  </div>
  <div class="contact contact--email">
    <svg viewBox="0 0 28 30" aria-hidden="true">
      <path d="M14,2 L26,7 V15 C26,22 20,27 14,29 C8,27 2,22 2,15 V7 Z" fill="var(--amber)"/>
      <path d="M15,1 L26,6 V14 C26,21 21,26 15,28 C9,26 4,21 4,14 V6 Z" fill="var(--navy)"/>
      <rect x="10" y="10" width="10" height="7" fill="#fff"/>
      <polyline points="10,10 15,14 20,10" fill="none" stroke="var(--navy)" stroke-width="1"/>
    </svg>
    <span>hello@shiftwellhealth.com</span>
  </div>
  <div class="contact contact--web">
    <svg viewBox="0 0 28 30" aria-hidden="true">
      <path d="M14,2 L26,7 V15 C26,22 20,27 14,29 C8,27 2,22 2,15 V7 Z" fill="var(--amber)"/>
      <path d="M15,1 L26,6 V14 C26,21 21,26 15,28 C9,26 4,21 4,14 V6 Z" fill="var(--navy)"/>
      <circle cx="15" cy="13.5" r="5" fill="none" stroke="#fff" stroke-width="1.2"/>
      <ellipse cx="15" cy="13.5" rx="2.2" ry="5" fill="none" stroke="#fff" stroke-width="1"/>
      <line x1="10" y1="13.5" x2="20" y2="13.5" stroke="#fff" stroke-width="1"/>
    </svg>
    <span>www.shiftwellhealth.com</span>
  </div>
</section>

</body>
</html>
```